PostCard Design Project

I am making a mailing postcard
I am having the mailing printed using 4 color foil on certain parts.
I am looking for a design that maximizes the foil process where certain parts are done in foil to grab the customers attention (example: if there is a car on the postcard the headlights would be done in foil) .
I am targeting some industries, (auto, real estate, medical, beauty) I would like the post card to have examples of postcard ideas for 2 or 3 of these industries.
specs:
the postcard should be atleast 6.5x9 up to 8.5x11, I don't want to restrict the space for the creative as I don't want everything to look like a huge mess. both sides will be used.
the piece is a direct mail piece so it has to meet requirements of https://www.mailvantor.com/business/pdf/quick-reference-guide.pdf
text will be
"business with no limits, meet mailing with no addresses, gain new customers through "Open Porch Route Drop" reach new customers at their home without needing their address. "
I also want some current print specials I am running included.
-double your order FREE (order 500 business cards and get 1000)
-250 100lb gloss stock brochures 99.00
-business packages (cards, envelopes and letterhead) 299
-1000 flyers 140.40
-5000 postcards 179.99
A list of services
banners
booklets
brochures
business cards
calendars
catalogs
CD/DVD packages
envelopes
event tickets
flyers
hangtags
postcards
posters
presentation folders
rack cards
labels
table tents
window cling and decal
"order 24/7 orders@inkwillow.com" must be included
my logo is InkWillow will be supplied later
ive received some great designs. however Im looking for something a little more modern like some zorvel would put out. if the amount of words is too much please feel free to edit. also an idea i had for the list of services i offer is to have it transparent yet readable as the background of the postcard some small some big but covering the entire backgroud. you can then design on top of that with other thing. just an early morning thought
Reason: I have uploaded a sketch of my idea, please take time to look at it for an accurate depiction of what im looking for. feel free to add elements that make it pop off the page
Reason: We are getting close i will be providing feed back today

```html
<!DOCTYPE html>
<html lang="en">
<head>
<meta charset="utf-8">
<title>InkWillow Mailing Postcard</title>
<link rel="stylesheet" href="https://fonts.googleapis.com/css2?family=Inconsolata:wght@400;500&family=Open+Sans:wght@300;400&family=Arimo:wght@400;700&family=Archivo+Narrow:ital,wght@1,700&display=swap">
<style>
  :root {
    --page: #d8d3cc;
    --card-blue: #1c8fd3;
    --card-edge: #1779b4;
    --white: #ffffff;
    --ink: #111111;
    --highlight: #f4ec3a;
    --bubble-top: #ffffff;
    --bubble-bottom: #dcdcdc;
    --photo-frame: #166a9c;
  }
  * { box-sizing: border-box; margin: 0; padding: 0; }
  html, body { width: 841px; height: 1200px; overflow: hidden; }
  body { background: var(--page); position: relative; font-family: "Arimo", Arial, sans-serif; }

  .postcard {
    position: absolute; left: 87px; width: 670px; height: 484px;
    background: var(--card-blue);
    box-shadow: 0 4px 14px rgba(0,0,0,.28);
    overflow: hidden;
  }
  .postcard--front { top: 98px; }
  .postcard--back { top: 627px; }

  /* Front */
  .headline {
    position: absolute; left: 21px; top: 19px;
    font-family: "Inconsolata", "Consolas", monospace; font-weight: 400;
    color: var(--white); font-size: 45px; line-height: 44px; letter-spacing: 1.3px;
    white-space: nowrap;
  }
  .headline__shine { display: block; font-size: 74px; line-height: 72px; margin-top: 8px; letter-spacing: 1px; }

  .brand {
    position: absolute; left: 431px; top: 10px; width: 171px; height: 60px;
    background: var(--white);
    display: flex; align-items: center; justify-content: center; gap: 8px;
  }
  .brand__dot { width: 22px; height: 22px; border-radius: 50%; background: var(--card-blue); }
  .brand__name { font-family: "Arimo", Arial, sans-serif; font-size: 24px; font-weight: 400; color: var(--card-edge); }

  .photo { position: absolute; display: block; }
  .photo--smile { left: 358px; top: 83px; width: 269px; height: 181px; }
  .photo--beauty { left: 125px; top: 198px; width: 286px; height: 184px; }
  .photo--headlight { left: 366px; top: 277px; width: 275px; height: 189px; background: var(--photo-frame); }
  .photo--headlight svg { position: absolute; left: 3px; top: 3px; }

  .contact {
    position: absolute; left: 21px; top: 385px;
    font-family: "Open Sans", Arial, sans-serif; font-weight: 300; color: var(--white);
    font-size: 29px; line-height: 42px; white-space: nowrap;
  }

  /* Back */
  .intro {
    position: absolute; left: 14px; top: 9px;
    font-size: 15px; line-height: 21px; color: var(--white); letter-spacing: 1.1px;
    white-space: nowrap;
  }
  .intro__program { color: var(--highlight); }

  .indicia {
    position: absolute; left: 568px; top: 20px; width: 81px; height: 78px;
    background: var(--white); border: 1px solid var(--ink);
    font-size: 10px; line-height: 12px; text-align: center; color: var(--ink);
    padding-top: 5px;
  }
  .indicia__paid { font-size: 12px; line-height: 14px; }

  .address-block {
    position: absolute; left: 492px; top: 113px; width: 157px; height: 84px;
    background: var(--white); border: 1px solid var(--ink);
    font-size: 13px; line-height: 17px; color: var(--ink);
    padding: 12px 0 0 16px;
  }

  .services__title {
    position: absolute; left: 325px; top: 91px;
    font-size: 36px; font-weight: 700; color: var(--highlight); line-height: 44px;
  }
  .services__list {
    position: absolute; left: 316px; top: 130px; list-style: none;
    font-family: "Inconsolata", "Consolas", monospace; font-size: 16px; line-height: 21.2px;
    color: var(--white); letter-spacing: 1.4px; white-space: nowrap;
  }
  .services__list li { position: relative; padding-left: 20px; }
  .services__list li::before {
    content: ""; position: absolute; left: 0; top: 8px; width: 5px; height: 5px;
    border-radius: 50%; background: var(--dot, var(--white));
  }

  .specials__title {
    position: absolute; left: 163px; top: 146px;
    font-family: "Archivo Narrow", "Arial Narrow", sans-serif; font-weight: 700; font-style: italic;
    color: var(--highlight); font-size: 23px; line-height: 21px;
  }
  .special {
    position: absolute; border-radius: 16px;
    background: linear-gradient(var(--bubble-top), var(--bubble-bottom));
    color: var(--ink); font-weight: 700; font-size: 13px; line-height: 18px;
    text-align: center; display: flex; align-items: center; justify-content: center;
    padding: 0 4px; white-space: nowrap;
  }
  .special--double { left: 7px; top: 162px; width: 155px; height: 116px; }
  .special--brochures { left: 165px; top: 216px; width: 123px; height: 99px; }
  .special--packages { left: 7px; top: 293px; width: 155px; height: 113px; }
  .special--postcards { left: 165px; top: 319px; width: 120px; height: 97px; padding-top: 18px; }
  .special--flyers { left: 87px; top: 406px; width: 95px; height: 55px; }
</style>
</head>
<body>

<section class="postcard postcard--front">
  <h1 class="headline">Let Us Help<br>Your Business<span class="headline__shine">SHINE!</span></h1>

  <div class="brand">
    <span class="brand__dot"></span>
    <span class="brand__name">InkWillow</span>
  </div>

  <svg class="photo photo--smile" role="img" aria-label="Close-up photo of a smile with dental braces" width="269" height="181" viewBox="0 0 269 181">
    <defs>
      <linearGradient id="smileTone" x1="0" y1="0" x2="1" y2="1">
        <stop offset="0" stop-color="#e2a98f"/>
        <stop offset=".55" stop-color="#b5534f"/>
        <stop offset="1" stop-color="#d89a84"/>
      </linearGradient>
    </defs>
    <rect width="269" height="181" fill="url(#smileTone)"/>
  </svg>

  <svg class="photo photo--beauty" role="img" aria-label="Beauty portrait photo of a woman" width="286" height="184" viewBox="0 0 286 184">
    <defs>
      <linearGradient id="beautyTone" x1="0" y1="0" x2="1" y2="0">
        <stop offset="0" stop-color="#f4f6f8"/>
        <stop offset=".45" stop-color="#e6cbbb"/>
        <stop offset="1" stop-color="#f1f3f5"/>
      </linearGradient>
    </defs>
    <rect width="286" height="184" fill="url(#beautyTone)"/>
  </svg>

  <div class="photo photo--headlight">
    <svg role="img" aria-label="Photo of a red sports car headlight" width="269" height="183" viewBox="0 0 269 183">
      <defs>
        <linearGradient id="headlightTone" x1="0" y1="0" x2="0" y2="1">
          <stop offset="0" stop-color="#c8202a"/>
          <stop offset=".5" stop-color="#3a3a40"/>
          <stop offset="1" stop-color="#141416"/>
        </linearGradient>
      </defs>
      <rect width="269" height="183" fill="url(#headlightTone)"/>
    </svg>
  </div>

  <p class="contact">24 hr/7day<br>Order@inkwillow.com</p>
</section>

<section class="postcard postcard--back">
  <p class="intro">Business with no limits, meet mailing with<br>no addresses, gain new customers through<br><span class="intro__program">"Open Porch Route Drop"</span><br>reach new customers at their home<br>without needing their address.</p>

  <div class="indicia">PRSRT STD<br>ECRWSS<br>U.S.POSTAGE<br><span class="indicia__paid">PAID</span><br>OPRD Retail</div>

  <div class="address-block">Local<br>Postal Customer</div>

  <h2 class="services__title">Services</h2>
  <ul class="services__list">
    <li style="--dot:#3aa64a">Banners</li>
    <li style="--dot:#45b4ea">Booklets</li>
    <li style="--dot:#2a4fa8">Brochures</li>
    <li style="--dot:#9a3fa0">Business cards</li>
    <li style="--dot:#f1e43a">Calendars</li>
    <li style="--dot:#e85a2a">Catalogs</li>
    <li style="--dot:#d2337e">CD/DVD packages</li>
    <li style="--dot:#f39a1e">Envelopes</li>
    <li style="--dot:#c9dc3a">Event tickets</li>
    <li style="--dot:#2fa046">Flyers</li>
    <li style="--dot:#1e7e6e">Hangtags</li>
    <li style="--dot:#d8312c">Postcards</li>
    <li style="--dot:#3fa0d8">Posters</li>
    <li style="--dot:#1b3f8a">Presentation folders</li>
    <li style="--dot:#6b3a9a">Rackcards</li>
    <li style="--dot:#e8a0b0">Labels</li>
  </ul>

  <p class="specials__title">current<br>specials<br>print</p>
  <div class="special special--double">Double your<br>order FREE<br>(order 500 business<br>cards and get 1000)</div>
  <div class="special special--brochures">250 100lb gloss<br>stock<br>brochures 99.00</div>
  <div class="special special--packages">Business packages<br>(cards, envelopes<br>and letterhead) 299</div>
  <div class="special special--postcards">5000 postcards<br>179.99</div>
  <div class="special special--flyers">1000 flyers<br>140.40</div>
</section>

</body>
</html>
```